Business Card Design

we are a small based family business that specialise in 12v led lights for velmora caravans.
we also sell 12v switches, wire, circuit breakers, dimmers etc but our main line is LEDs.
We would like something that reflects the LED lighting on our cards.
www.ridgeglowleds.com.au is where you can have a look at to get ideas, of our product.
I have attached the logo we generally use on all our tradix listings and is the main header on our website.

Look forward to seeing what your team comes up with.

Industry/Entity Type

Business

Contact Information for Business Card

Tam 0438 207 915
Quorrin Vale QLD 4399

www.ridgeglowleds.com

```html
<!DOCTYPE html>
<html lang="en">
<head>
<meta charset="utf-8">
<title>Ridgeglow LEDs – Business Card</title>
<link href="https://fonts.googleapis.com/css2?family=Open+Sans:wght@400;700;800&display=swap" rel="stylesheet">
<style>
  :root {
    --rust: #a42c12;
    --ink: #141414;
    --paper: #ffffff;
    --stage: #e9e7e4;
    --card-shadow: rgba(0, 0, 0, 0.18);
  }
  * { margin: 0; padding: 0; box-sizing: border-box; }
  html, body { width: 1200px; height: 900px; overflow: hidden; }
  body {
    background: var(--stage);
    font-family: "Open Sans", Arial, sans-serif;
    display: flex;
    align-items: center;
    justify-content: center;
    gap: 40px;
  }
  .card {
    position: relative;
    width: 540px;
    height: 308px;
    border-radius: 30px;
    overflow: hidden;
    background: var(--paper);
    box-shadow: 0 10px 28px var(--card-shadow);
  }
  .card-art { position: absolute; inset: 0; width: 100%; height: 100%; }
  .holder { position: absolute; left: 38px; top: 28px; color: var(--paper); }
  .holder-name { font-size: 22px; font-weight: 700; line-height: 1.2; }
  .holder-role { font-size: 17px; font-weight: 400; line-height: 1.3; }
  .contact-list {
    position: absolute; left: 34px; top: 140px;
    list-style: none; color: var(--paper);
    font-size: 12.5px; line-height: 1.45;
  }
  .contact-list li { display: flex; align-items: flex-start; gap: 7px; }
  .contact-list svg { flex: none; width: 12px; height: 12px; margin-top: 3px; }
  .wordmark {
    position: absolute;
    font-weight: 800;
    color: var(--ink);
    text-transform: uppercase;
    line-height: 0.95;
    letter-spacing: 0.5px;
    white-space: nowrap;
  }
  .card-front .wordmark { right: 30px; bottom: 40px; font-size: 33px; text-align: left; }
  .card-back .wordmark { left: 50%; top: 50%; transform: translate(-50%, -50%); font-size: 44px; }
</style>
</head>
<body>

  <section class="card card-front">
    <svg class="card-art" viewBox="0 0 350 200" preserveAspectRatio="none" aria-hidden="true">
      <rect width="350" height="200" fill="var(--rust)"/>
      <path d="M350,52 C250,50 150,100 82,200 H350 Z" fill="var(--ink)"/>
      <path d="M350,60 C262,62 170,115 106,200 H350 Z" fill="var(--paper)"/>
    </svg>

    <div class="holder">
      <p class="holder-name">Aldo Brenner</p>
      <p class="holder-role">Owner / C.E.O</p>
    </div>

    <ul class="contact-list">
      <li>
        <svg viewBox="0 0 12 12"><circle cx="6" cy="6" r="6" fill="#fff"/><path d="M6 2.5a2 2 0 0 1 2 2c0 1.5-2 4-2 4s-2-2.5-2-4a2 2 0 0 1 2-2z" fill="var(--rust)"/></svg>
        <span>Suite # 118, Fenn Bldg,<br>NY 40917</span>
      </li>
      <li>
        <svg viewBox="0 0 12 12"><circle cx="6" cy="6" r="6" fill="#fff"/><path d="M4 3l1.3 1.6-.7.8c.5 1 1.1 1.6 2 2l.8-.7L9 8l-.7 1.1C6 9 3.5 6.4 3 3.8z" fill="var(--rust)"/></svg>
        <span>214-385-0962</span>
      </li>
      <li>
        <svg viewBox="0 0 12 12"><circle cx="6" cy="6" r="6" fill="#fff"/><rect x="4.2" y="2.6" width="3.6" height="6.8" rx="0.6" fill="var(--rust)"/></svg>
        <span>906-731-4258</span>
      </li>
      <li>
        <svg viewBox="0 0 12 12"><circle cx="6" cy="6" r="6" fill="#fff"/><rect x="3" y="5" width="6" height="3.6" fill="var(--rust)"/><rect x="4" y="3" width="4" height="2" fill="var(--rust)"/></svg>
        <span>573-618-2049</span>
      </li>
      <li>
        <svg viewBox="0 0 12 12"><circle cx="6" cy="6" r="6" fill="#fff"/><rect x="3" y="4" width="6" height="4.2" fill="var(--rust)"/><path d="M3 4l3 2.3L9 4" stroke="#fff" stroke-width="0.7" fill="none"/></svg>
        <span>name@ridgeglowleds.com</span>
      </li>
      <li>
        <svg viewBox="0 0 12 12"><circle cx="6" cy="6" r="6" fill="#fff"/><circle cx="6" cy="6" r="3.2" fill="none" stroke="var(--rust)" stroke-width="0.8"/><path d="M2.8 6h6.4M6 2.8c-1.4 1.8-1.4 4.6 0 6.4M6 2.8c1.4 1.8 1.4 4.6 0 6.4" stroke="var(--rust)" stroke-width="0.6" fill="none"/></svg>
        <span>www.ridgeglowleds.com</span>
      </li>
    </ul>

    <p class="wordmark">Ridgeglow<br>LEDs</p>
  </section>

  <section class="card card-back">
    <p class="wordmark">Ridgeglow<br>LEDs</p>
  </section>

</body>
</html>
```